Advanced Therapeutic Massage Therapist

I need a business card advertising my massage services as an advanced therapeutic massage therapist. I offer advanced therapeutic massage, swedish and deep tissue. I want to create a simple, professional and feminine card. I like bright colours and creativity.

I prefer a bold and experimental approach rather than something status-quo. A card to suggest therapeutic healing through dynamic massage. Motifs, shapes or layout which suggest movement and flow.
Updates

Target Market(s)

Everybody!

Industry/Entity Type

Health And Wellness

Contact Information for Business Card

The card should include:
My name, logo, services offered and my contact details.

Sláine Dunleavy
Massage Therapist

- Swedish - Deep Tissue - Advanced Therapeutic

Phone: (+353) 87 216 4093
Email: regenerate@slainedunleavy-example.com
Website: www.slainedunlevy-example.com

Font styles to use
Serif
Sans Serif
Decorative
Script

Colors

Designer to choose colors to be used in the design.

Requirements
Must have
• An example may contain something like this, yet concise:
• "Sláine Dunleavy
• Massage Therapist
• - Swedish - Deep Tissue - Advanced Therapeutic"
Nice to have
• This sentence is optional:
• Imagery such as a logo or symbol. I have attached a file containing a logo I had produced however the name is incorrect now as it is "Sláine" not "Nelly". It could be edited to change it to Sláine.
• I have sent the file as .psd .jpg. .pdf and .png
• I like when the card conveys energy, movement, pressure points, flow etc.
• I just like the designer to follow their own style and ideas. I like bright colours but must have a lot of a base colour to offset it. I really prefer them to follow their own inspiration. That is my preference.
Should not have
• Pine trees, non-native trees to Britain and Ireland, exotic flowers or animals that are not native to Britain and Ireland.
• I don't like brown as the background colour of the card.
• The cars shouldn't look like a wedding invitation i.e too many floral type designs.

```html
<!DOCTYPE html>
<html lang="en">
<head>
<meta charset="utf-8">
<title>Sláine Dunleavy – Massage Therapist Business Card</title>
<link rel="stylesheet" href="https://fonts.googleapis.com/css2?family=Allura&family=Questrial&family=Barlow+Semi+Condensed:wght@500&display=swap">
<style>
  :root {
    --backdrop: #676767;
    --card-base: #232323;
    --ink-light: #f4f4f2;
    --teal-soft: #a9dccb;
    --teal-pale: #cdeee2;
    --teal-text: #6cc3a3;
    --gold: #e9c54a;
    --gold-deep: #a8782a;
    --contact-ink: #1e1e1e;
  }
  * { margin: 0; padding: 0; box-sizing: border-box; }
  html, body {
    width: 1200px; height: 550px; overflow: hidden;
    background: var(--backdrop);
  }
  .card {
    position: absolute; top: 158px;
    width: 391px; height: 235px;
    background: var(--card-base);
    overflow: hidden;
    box-shadow: 0 0 0 1px rgba(255,255,255,0.08);
  }
  .card--front { left: 195px; }
  .card--back { left: 614px; }

  .emblem {
    position: absolute; border-radius: 50%;
    background: radial-gradient(circle at 50% 45%, var(--teal-pale) 0%, var(--teal-soft) 60%, #8fc9b4 100%);
    box-shadow: 0 0 0 4px var(--gold-deep), 0 0 0 6px rgba(233,197,74,0.3);
  }
  .card--front .emblem { width: 104px; height: 104px; left: 143px; top: 36px; }
  .card--back .emblem { width: 120px; height: 120px; left: 50px; top: 36px; }

  .name {
    font-family: "Allura", cursive;
    color: var(--ink-light);
    font-weight: 400; line-height: 1;
    white-space: nowrap;
  }
  .role {
    font-family: "Questrial", sans-serif;
    color: var(--ink-light);
    letter-spacing: 0.9px; line-height: 1;
    white-space: nowrap;
  }

  .card--front .identity {
    position: absolute; left: 0; width: 100%; top: 150px; text-align: center;
  }
  .card--front .name { font-size: 28px; }
  .card--front .role { font-size: 10px; margin-top: 0; }

  .tagline {
    position: absolute; left: 0; width: 100%; top: 209px; text-align: center;
    font-family: "Barlow Semi Condensed", sans-serif; font-weight: 500;
    font-size: 10.5px; color: var(--teal-text);
  }

  .card--back .identity {
    position: absolute; right: 24px; top: 30px; text-align: center;
  }
  .card--back .name { font-size: 30px; }
  .card--back .role { font-size: 10.5px; margin-top: 2px; }

  .flow { position: absolute; inset: 0; width: 391px; height: 235px; }

  .contact {
    position: absolute; right: 18px; top: 172px;
    list-style: none; text-align: right;
    font-family: "Questrial", sans-serif; font-size: 10.5px;
    color: var(--contact-ink);
  }
  .contact li {
    display: flex; justify-content: flex-end; align-items: center;
    gap: 6px; height: 17px;
  }
  .contact svg { width: 9px; height: 9px; fill: var(--contact-ink); }
</style>
</head>
<body>

<section class="card card--front">
  <div class="emblem" role="img" aria-label="Circular tree-of-life emblem in gold on a soft teal disc"></div>
  <div class="identity">
    <div class="name">Sláine Dunleavy</div>
    <div class="role">massage therapist</div>
  </div>
  <p class="tagline">AMTQ qualified, specializing in Advanced Therapeutic &amp; Deep Tissue Massage</p>
</section>

<section class="card card--back">
  <svg class="flow" viewBox="0 0 391 235" aria-hidden="true">
    <defs>
      <linearGradient id="goldSheen" x1="0" y1="0" x2="1" y2="0">
        <stop offset="0" stop-color="#c99a2e"/>
        <stop offset="0.5" stop-color="#f6d65c"/>
        <stop offset="1" stop-color="#e9c54a"/>
      </linearGradient>
      <linearGradient id="tealWash" x1="0" y1="0" x2="1" y2="1">
        <stop offset="0" stop-color="#bfe8da"/>
        <stop offset="0.6" stop-color="#a6dccb"/>
        <stop offset="1" stop-color="#c9ece0"/>
      </linearGradient>
    </defs>
    <path d="M0,204 C110,220 190,210 260,172 C310,146 350,135 391,132 L391,235 L0,235 Z" fill="url(#tealWash)"/>
    <path d="M0,186 C100,201 170,196 245,161 C300,135 345,121 391,116 L391,124 C345,129 300,143 250,169 C180,205 100,208 0,193 Z" fill="url(#goldSheen)"/>
    <path d="M0,196 C70,206 140,208 200,194 C150,210 70,208 0,201 Z" fill="url(#goldSheen)"/>
  </svg>

  <div class="emblem" role="img" aria-label="Circular tree-of-life emblem in gold on a soft teal disc"></div>

  <div class="identity">
    <div class="name">Sláine Dunleavy</div>
    <div class="role">massage therapist</div>
  </div>

  <ul class="contact">
    <li>(+353) 87 216 4093
      <svg viewBox="0 0 10 10"><path d="M1,3 C1,1.5 3,1 5,1 C7,1 9,1.5 9,3 L7.5,4 L6.5,3 L3.5,3 L2.5,4 Z M2,5 L8,5 L9,9 L1,9 Z"/></svg>
    </li>
    <li>slainedunleavy-example.com
      <svg viewBox="0 0 10 10"><path d="M0,2 L10,2 L10,8 L0,8 Z M0.8,2.6 L5,5.6 L9.2,2.6" stroke="#fff" stroke-width="0.7"/></svg>
    </li>
    <li>slaine@slainedunleavy-example.com
      <svg viewBox="0 0 10 10"><circle cx="5" cy="5" r="4.5"/><path d="M0.5,5 H9.5 M5,0.5 V9.5 M5,0.5 C2.5,3 2.5,7 5,9.5 M5,0.5 C7.5,3 7.5,7 5,9.5" stroke="#fff" stroke-width="0.6" fill="none"/></svg>
    </li>
  </ul>
</section>

</body>
</html>
```